The design should look similar to the uploaded example to accommodate the information needed for a business card template. I would like to see the colors orange and charcoal grey incorporated along with the logo.The following should be on the back of the card SPECIALIZING IN NEW AND USED TIRES & WHEELS FOR:- Loaders- Skid Steers- Telehandlers- Boom Lifts- Forklifs and moreELIMINATING DOWNTIMEWheel Exchange Program for New & Used Foam Filled and Solid Rubber TiresSPECIALTY SERVICES- Foam Filling Tires- Largest Tire Press in SE- ONSITE Forklift Tire Press- Boom Truck Services - Rubber Tracks

Target Market(s)

New and Existing Customers

Industry/Entity Type

Business

Contact Information for Business Card

NAMEHEAVY DUTY TIRE, LLC8470 Belvedere RoadWest Palm Beach, FL 33411P: 844-HD-TIRESF: 561-431-6469C:E: W: WWW.GRANITERIMSUPPLY-EXAMPLE.COM

Font styles to use
Sans Serif

Colors
f37122
333333

Requirements
Must have
• The logo and the information indicated for the backside of the card
Nice to have
• Keep the orange and charcoal grey colors

```html
<!DOCTYPE html>
<html lang="en">
<head>
<meta charset="utf-8">
<title>Granite Rim Supply, LLC – Business Card</title>
<link rel="stylesheet" href="https://fonts.googleapis.com/css2?family=Roboto+Slab:wght@400;700&display=swap">
<style>
  :root {
    --orange: #f37122;
    --charcoal: #333333;
    --charcoal-deep: #3a3f3f;
    --white: #ffffff;
    --backdrop: #e8e5e0;
    --font: "Roboto Slab", serif;
  }
  * { box-sizing: border-box; margin: 0; padding: 0; }
  html, body { width: 1200px; height: 843px; overflow: hidden; }
  body { background: var(--backdrop); font-family: var(--font); position: relative; }

  .card {
    position: absolute;
    width: 620px; height: 354px;
    background: var(--charcoal-deep);
    overflow: hidden;
    box-shadow: 0 6px 18px rgba(0,0,0,.18);
  }
  .card-services { left: 520px; top: 50px; }
  .card-contact  { left: 60px;  top: 440px; }
  .card-shape { position: absolute; inset: 0; width: 620px; height: 354px; }

  /* brand mark: plain circle + name */
  .brand { position: absolute; display: flex; align-items: center; gap: 12px; }
  .brand-dot { width: 34px; height: 34px; border-radius: 50%; background: var(--orange); flex: none; }
  .brand-name { font-weight: 700; color: var(--charcoal); line-height: 1.15; text-transform: uppercase; }

  .card-services .brand { left: 22px; top: 0; height: 354px; width: 250px; }
  .card-services .brand-name { font-size: 19px; }

  .services {
    position: absolute; right: 26px; top: 26px; width: 300px;
    text-align: right; color: var(--white);
  }
  .services-heading { color: var(--orange); font-weight: 700; font-size: 12.5px; line-height: 1.3; text-transform: uppercase; margin-bottom: 4px; }
  .services-heading + .services-list { margin-bottom: 12px; }
  .services-list { list-style: none; font-size: 11.5px; line-height: 1.45; }
  .bullet { color: var(--orange); }

  .contact { position: absolute; left: 34px; top: 36px; color: var(--white); }
  .contact-name { color: var(--orange); font-size: 20px; font-weight: 700; letter-spacing: .5px; }
  .contact-title { font-size: 12.5px; margin-bottom: 10px; letter-spacing: .5px; }
  .contact-address { font-size: 12.5px; line-height: 1.4; margin-bottom: 6px; }
  .contact-lines { list-style: none; font-size: 12.5px; line-height: 1.55; }
  .contact-lines li { display: flex; align-items: center; gap: 8px; }
  .icon { width: 12px; height: 12px; flex: none; fill: var(--orange); }

  .card-contact .brand { left: 395px; top: 0; height: 354px; width: 215px; }
  .card-contact .brand-name { font-size: 18px; }
</style>
</head>
<body>

<section class="card card-services" aria-label="Card back: services">
  <svg class="card-shape" viewBox="0 0 620 354" aria-hidden="true">
    <path d="M0 0 H244 L304 66 V288 L244 354 H0 Z" fill="none" stroke="var(--orange)" stroke-width="10"/>
    <path d="M0 0 H228 L288 66 V288 L228 354 H0 Z" fill="var(--white)"/>
  </svg>
  <div class="brand">
    <span class="brand-dot"></span>
    <span class="brand-name">Granite Rim<br>Supply</span>
  </div>
  <div class="services">
    <h2 class="services-heading">Specializing in new and<br>used tires &amp; wheels for</h2>
    <ul class="services-list">
      <li>Loaders <span class="bullet">•</span> Skid Steers <span class="bullet">•</span> Telehandlers</li>
      <li>Boom Lifts <span class="bullet">•</span> Forklifts and more</li>
    </ul>
    <h2 class="services-heading">Specialty Services</h2>
    <ul class="services-list">
      <li>Foam Filling Tires <span class="bullet">•</span></li>
      <li>Largest Tire Press in SE <span class="bullet">•</span></li>
      <li>ONSITE Forklift Tire Press <span class="bullet">•</span></li>
      <li>Boom Truck Services <span class="bullet">•</span></li>
      <li>Rubber Tracks <span class="bullet">•</span></li>
    </ul>
    <h2 class="services-heading">Eliminating Downtime</h2>
    <ul class="services-list">
      <li>Wheel Exchange Program for New &amp;</li>
      <li>Used Foam Filled &amp; Solid Rubber Tires</li>
    </ul>
  </div>
</section>

<section class="card card-contact" aria-label="Card front: contact">
  <svg class="card-shape" viewBox="0 0 620 354" aria-hidden="true">
    <path d="M620 0 H376 L316 66 V288 L376 354 H620 Z" fill="none" stroke="var(--orange)" stroke-width="10"/>
    <path d="M620 0 H392 L332 66 V288 L392 354 H620 Z" fill="var(--white)"/>
  </svg>
  <div class="contact">
    <h1 class="contact-name">DANIEL REYES</h1>
    <p class="contact-title">CEO/FOUNDER</p>
    <p class="contact-address">5126 Marston Lane<br>Lake Arden, FL 33907</p>
    <ul class="contact-lines">
      <li><svg class="icon" viewBox="0 0 12 12"><path d="M2.5 0.5 L4.5 0.5 L5.2 3.2 L3.8 4.3 Q5 7 7.7 8.2 L8.8 6.8 L11.5 7.5 V9.5 Q11.5 11.5 9.5 11.5 Q0.5 11 0.5 2.5 Q0.5 0.5 2.5 0.5Z"/></svg>844-GR-WHEEL</li>
      <li><svg class="icon" viewBox="0 0 12 12"><rect x="1" y="3" width="10" height="7" rx="1"/><rect x="3" y="0.5" width="6" height="3" fill="var(--white)"/></svg>836 517 2048</li>
      <li><svg class="icon" viewBox="0 0 12 12"><rect x="3" y="0.5" width="6" height="11" rx="1.2"/></svg>561-278-9053</li>
      <li><svg class="icon" viewBox="0 0 12 12"><rect x="0.5" y="2" width="11" height="8" rx="1"/><path d="M1 2.5 L6 6.5 L11 2.5" stroke="var(--charcoal-deep)" fill="none"/></svg>name@graniterimsupply-example.com</li>
      <li><svg class="icon" viewBox="0 0 12 12"><circle cx="6" cy="6" r="5.5"/></svg>graniterimsupply-example.com</li>
    </ul>
  </div>
  <div class="brand">
    <span class="brand-dot"></span>
    <span class="brand-name">Granite Rim<br>Supply LLC</span>
  </div>
</section>

</body>
</html>
```